Brookvane Consulting Business Card Design

Business Card Design for Brookvane Consulting. Brookvane Consulting is a boutique consultancy based in Atlanta, GA., that specializes in marketing strategy, organization planning, and leadership development. We provide solutions for small businesses and startups as well as Vantage 300 companies.

http://brookvaneconsulting.com/

Target Market(s)

We provide solutions for small businesses and startups as well as Vantage 300 companies.

Industry/Entity Type

Consulting

Contact Information for Business Card

Two sided business card with priority on contact information, logo, tag line (Inspiration to Dream More, Do More, Become More)

Colors

Designer to choose colors to be used in the design.

Requirements
Must have
• contact information, logo, tag line (Inspiration to Dream More, Do More, Become More)
• Simple no over communication.
Nice to have
• I would like to see different placements of logo and creative use of both sides of the card
Should not have
• Do not put too much information on the card.

```html
<!DOCTYPE html>
<html lang="en">
<head>
<meta charset="utf-8">
<title>Brookvane Consulting – Business Card</title>
<link href="https://fonts.googleapis.com/css2?family=Lato:wght@400;700&family=Damion&display=swap" rel="stylesheet">
<style>
  :root {
    --backdrop: #ece6dc;
    --card-dark: #333333;
    --card-light: #ffffff;
    --ink-light: #ffffff;
    --ink-dark: #2e2e2e;
    --ink-soft: #d9d9d9;
  }
  * { margin: 0; padding: 0; box-sizing: border-box; }
  html, body {
    width: 1200px; height: 900px; overflow: hidden;
    background: var(--backdrop);
    font-family: "Lato", Arial, sans-serif;
  }
  .canvas { position: relative; width: 1200px; height: 900px; }
  .card-shapes { position: absolute; inset: 0; }
  .card-dark { fill: var(--card-dark); }
  .card-light { fill: var(--card-light); }

  .holder { position: absolute; left: 176px; top: 341px; color: var(--ink-light); }
  .holder-name { font-weight: 700; font-size: 15px; letter-spacing: 0.2px; text-transform: uppercase; }
  .holder-role { font-size: 13px; margin-top: 1px; color: var(--ink-soft); }

  .brand-name {
    position: absolute;
    font-family: "Lato", Arial, sans-serif;
    font-weight: 400;
    font-size: 27px;
    line-height: 1.05;
    text-align: right;
  }
  .brand-name--front { right: 695px; top: 410px; color: var(--ink-light); }
  .brand-name--back { left: 670px; top: 410px; text-align: left; color: var(--ink-dark); }

  .contact-list {
    position: absolute; left: 176px; top: 502px;
    list-style: none; color: var(--ink-light); font-size: 13px;
  }
  .contact-list li { display: flex; align-items: center; gap: 4px; height: 16px; }
  .contact-list svg { width: 10px; height: 10px; fill: var(--ink-light); }

  .tagline {
    position: absolute; right: 177px; top: 386px;
    font-family: "Damion", cursive;
    font-size: 21px; line-height: 28px;
    color: var(--ink-dark); text-align: right;
  }
</style>
</head>
<body>
<main class="canvas">
  <svg class="card-shapes" width="1200" height="900" viewBox="0 0 1200 900" aria-hidden="true">
    <path class="card-dark" d="M150 305 H428 L582 440 Q596 455 582 470 L432 578 H150 Z"/>
    <path class="card-light" d="M1048 305 H770 L616 440 Q602 455 616 470 L768 578 H1048 Z"/>
  </svg>

  <section class="card-front">
    <div class="holder">
      <p class="holder-name">Marcus Hale</p>
      <p class="holder-role">Managing Director</p>
    </div>
    <p class="brand-name brand-name--front">Brookvane<br>Consulting</p>
    <ul class="contact-list">
      <li><svg viewBox="0 0 10 10"><path d="M2 0.5 L3.5 2.5 L2.6 3.6 Q3.6 5.8 6.4 7.4 L7.5 6.5 L9.5 8 L8.5 9.5 Q3 9 0.5 1.5 Z"/></svg>444 555 0192</li>
      <li><svg viewBox="0 0 10 10"><path d="M0 2 H10 V8.5 H0 Z M0.6 2.4 L5 5.6 L9.4 2.4" stroke="#333" stroke-width="0.8"/></svg>info@brookvaneconsulting.com</li>
      <li><svg viewBox="0 0 10 10"><circle cx="5" cy="5" r="4.6"/><path d="M5 0.4 V9.6 M0.4 5 H9.6" stroke="#333" stroke-width="0.7"/></svg>www.brookvaneconsulting.com</li>
    </ul>
  </section>

  <section class="card-back">
    <p class="brand-name brand-name--back">Brookvane<br>Consulting</p>
    <p class="tagline">Inspiration to<br>Dream More<br>Do More<br>Become More</p>
  </section>
</main>
</body>
</html>
```